Alloy wheel repair business needs a website

Install logo previously purchased from makerhive, toolbar with dropdowns. services, gallery, clients , contact ect
Maybe mission statment

Target Market(s)

vehicle owners, auto dealers,insurance companies,

Industry/Entity Type

Alloy Wheel Repair

Coding

Coded - Design and coding required

Number of Pages Required

4 page

Font styles to use
Sans Serif

Colors
0054AA
0677BA
7BADD7
CADEEF
E8F1F8

```html
<!DOCTYPE html>
<html lang="en">
<head>
<meta charset="utf-8">
<title>Rimcraft Wheel Works</title>
<link href="https://fonts.googleapis.com/css2?family=Exo+2:wght@600;700;800&family=Roboto:wght@400;500;700&display=swap" rel="stylesheet">
<style>
:root{
  --blue-deep:#0054AA;
  --blue:#0677BA;
  --blue-bright:#3f8fd6;
  --blue-soft:#7BADD7;
  --blue-pale:#CADEEF;
  --blue-mist:#E8F1F8;
  --ink:#1b1b1d;
  --text:#555b63;
  --white:#ffffff;
  --footer:#1a1a1c;
}
*{box-sizing:border-box;margin:0;padding:0}
html,body{width:1200px;height:4300px;overflow:hidden}
body{font-family:"Roboto",sans-serif;color:var(--text);background:var(--white);position:relative}
.abs{position:absolute}
.heading{font-family:"Exo 2",sans-serif;font-weight:800;letter-spacing:1px;color:var(--ink);text-transform:uppercase}
.heading .accent{color:var(--blue-bright)}
.btn{position:absolute;display:flex;align-items:center;justify-content:center;border-radius:22px;font:500 15px "Roboto",sans-serif;color:var(--white)}
.btn-blue{background:var(--blue-bright)}
.btn-dark{background:var(--ink)}

/* header */
.topline{left:0;top:0;width:1200px;height:5px;background:var(--blue-bright)}
.brand{display:flex;align-items:center;gap:10px;font-family:"Exo 2",sans-serif;font-weight:800;font-size:30px;color:var(--blue-deep);letter-spacing:1px}
.brand-dot{width:22px;height:22px;border-radius:50%;background:var(--blue-bright)}
.nav{display:flex;font-size:15px;color:var(--ink)}
.nav span{width:92px;text-align:center}
.call{display:flex;align-items:center;gap:10px;font-size:13px;color:var(--ink)}
.call b{display:block;font-size:15px}
.icon-circle{width:36px;height:36px;flex:none;border-radius:50%;background:var(--blue-bright);display:flex;align-items:center;justify-content:center}

/* hero */
.hero{left:0;top:150px;width:1200px;height:650px;background:linear-gradient(90deg,#1c1d20 0%,#2b2c30 38%,#4a4f57 60%,#2d4f7a 82%,#1e3e68 100%)}
.hero-title{left:110px;top:325px;font-family:"Exo 2",sans-serif;font-weight:800;font-size:62px;line-height:70px;color:var(--white);letter-spacing:2px}
.hero-title .accent{color:var(--blue-bright)}

/* services */
.section-title{left:0;width:1200px;text-align:center;font-size:48px}
.lead{left:150px;width:900px;text-align:center;font-size:13px;line-height:22px}
.card{position:absolute;top:1130px;width:260px;height:360px;background:var(--white);border-radius:16px;box-shadow:0 6px 24px rgba(0,0,0,.12);text-align:center}
.service-art{width:104px;height:104px;margin:30px auto 0;border-radius:50%;background:radial-gradient(circle at 62% 50%,var(--blue-bright) 0%,var(--blue) 38%,#1f2a38 62%,var(--ink) 100%);display:flex;align-items:center;justify-content:center;padding-left:12px;font:700 30px "Exo 2",sans-serif;color:var(--white)}
.card h3{font-family:"Roboto",sans-serif;font-weight:700;font-size:22px;color:var(--ink);margin-top:16px}
.card p{font-size:12.5px;line-height:19px;padding:10px 38px 0}
.card a{display:block;color:var(--blue);font-size:13px;font-weight:500;margin-top:18px}

/* mission */
.mission{left:0;top:1700px;width:1200px;height:600px;background:linear-gradient(180deg,var(--blue-bright),#3a88cf)}
.mission-photo{left:625px;top:1745px;width:490px;height:490px;border-radius:50%;background:radial-gradient(circle at 55% 45%,#9aa3ad,#4d5560 55%,#2c3138);border:6px solid rgba(255,255,255,.35)}

/* gallery */
.shot{position:absolute;border-radius:10px}
.overlay{background:rgba(20,60,120,.55);display:flex;align-items:center;justify-content:center;gap:12px}
.mini{width:34px;height:34px;border-radius:50%;background:var(--ink)}

/* contact */
.contact{left:0;top:3150px;width:1200px;height:725px;background:var(--blue-mist)}
.info{display:flex;gap:18px}
.info h4{font-family:"Exo 2",sans-serif;font-weight:700;font-size:22px;color:var(--ink);text-transform:uppercase}
.info p{font-size:13px;line-height:20px}
.field{position:absolute;background:var(--white);border-radius:4px;font-size:13px;padding:14px 18px;color:#888}
.social{width:34px;height:34px;border-radius:50%;background:var(--white);box-shadow:0 2px 6px rgba(0,0,0,.12);display:flex;align-items:center;justify-content:center}
.social::after{content:"";width:12px;height:12px;border-radius:50%;background:var(--blue-bright)}

/* footer */
.footer{left:0;top:3880px;width:1200px;height:420px;background:var(--footer);color:#d9dbe0}
.foot-row{left:0;width:1200px;display:flex;justify-content:center;gap:40px;font-size:14px;color:var(--white)}
.foot-social{width:24px;height:24px;border-radius:50%;background:var(--blue-bright)}
</style>
</head>
<body>

<header>
  <div class="abs topline"></div>
  <div class="abs brand" style="left:110px;top:48px"><span>RIMCRAFT WORKS</span><span class="brand-dot"></span></div>
  <div class="abs call" style="left:775px;top:40px">
    <div class="icon-circle"><svg width="16" height="16" viewBox="0 0 24 24"><path fill="#fff" d="M6.6 10.8a15 15 0 0 0 6.6 6.6l2.2-2.2c.3-.3.7-.4 1-.2 1.1.4 2.3.6 3.6.6.6 0 1 .4 1 1V20c0 .6-.4 1-1 1A17 17 0 0 1 3 4c0-.6.4-1 1-1h3.5c.6 0 1 .4 1 1 0 1.3.2 2.5.6 3.6.1.3 0 .7-.2 1z"/></svg></div>
    <div>Call Us:<b>555-214-0388</b></div>
  </div>
  <div class="btn btn-blue" style="left:960px;top:35px;width:130px;height:38px">Get A Quote</div>
  <nav class="abs nav" style="left:545px;top:95px"><span>Home</span><span>Services</span><span>Gallery</span><span>Clients</span><span>Contact</span></nav>
</header>

<section>
  <div class="abs hero" role="img" aria-label="Photo of a mechanic using an impact wrench on a car wheel in a workshop"></div>
  <h1 class="abs hero-title">WELCOME TO<br><span class="accent">RIMCRAFT WHEEL</span><br>WORKS</h1>
  <div class="btn btn-blue" style="left:110px;top:578px;width:125px;height:42px">Get Started</div>
</section>

<section>
  <h2 class="abs heading section-title" style="top:905px">Our <span class="accent">Services</span></h2>
  <p class="abs lead" style="top:1015px">Sed ut perspiciatis unde omnis iste natus error sit voluptatem accusantium doloremque laudantium, totam rem aperiam, eaque ipsa quae ab illo inventore veritatis et quasi architecto beatae vitae dicta sunt explicabo. Nemo enim ipsam voluptatem quia voluptas sit aspernatur aut.</p>

  <div class="card" style="left:105px">
    <div class="service-art" role="img" aria-label="Tyre illustration with a blue rim, service one">1</div>
    <h3>LOREM IPSUM</h3>
    <p>Lorem ipsum dolor sit amet, consectetur adipiscing elit, sed do eiusmod tempor incididunt ut labore et dolore magna aliqua. Quis ipsum suspendisse.</p>
    <a>View Details</a>
  </div>
  <div class="card" style="left:450px">
    <div class="service-art" role="img" aria-label="Tyre illustration with a blue rim, service two">2</div>
    <h3>LOREM IPSUM</h3>
    <p>Lorem ipsum dolor sit amet, consectetur adipiscing elit, sed do eiusmod tempor incididunt ut labore et dolore magna aliqua. Quis ipsum suspendisse.</p>
    <a>View Details</a>
  </div>
  <div class="card" style="left:790px">
    <div class="service-art" role="img" aria-label="Tyre illustration with a blue rim, service three">3</div>
    <h3>LOREM IPSUM</h3>
    <p>Lorem ipsum dolor sit amet, consectetur adipiscing elit, sed do eiusmod tempor incididunt ut labore et dolore magna aliqua. Quis ipsum suspendisse.</p>
    <a>View Details</a>
  </div>

  <div class="btn btn-blue" style="left:462px;top:1555px;width:126px;height:42px">View More</div>
  <div class="btn btn-dark" style="left:608px;top:1555px;width:126px;height:42px">Get Started</div>
</section>

<section>
  <div class="abs mission"></div>
  <h2 class="abs heading" style="left:110px;top:1775px;font-size:46px;color:var(--white)">Our Mission</h2>
  <div class="abs" style="left:110px;top:1845px;width:70px;height:4px;background:var(--white)"></div>
  <p class="abs" style="left:110px;top:1895px;width:480px;font-size:13px;line-height:22px;color:var(--white)">Sed ut perspiciatis unde omnis iste natus error sit voluptatem accusantium doloremque laudantium, totam rem aperiam, eaque ipsa quae ab illo inventore veritatis et quasi architecto beatae vitae dicta sunt explicabo. Nemo enim ipsam voluptatem quia voluptas sit aspernatur aut odit aut fugit, sed quia consequuntur magni dolores eos qui ratione voluptatem sequi nesciunt. Neque porro quisquam est, qui dolorem ipsum quia dolor sit amet, consectetur, adipisci velit, sed quia non numquam eius modi tempora incidunt ut labore et dolore magnam aliquam quaerat voluptatem.</p>
  <div class="btn btn-dark" style="left:110px;top:2148px;width:116px;height:40px">Read More</div>
  <div class="abs mission-photo" role="img" aria-label="Close-up photo of hands tightening the nuts of an alloy wheel"></div>
</section>

<section>
  <h2 class="abs heading section-title" style="top:2375px">Our <span class="accent">Gallery</span></h2>
  <div class="shot" style="left:115px;top:2495px;width:310px;height:210px;background:linear-gradient(135deg,#2d5f9a,#6f7c8a)" role="img" aria-label="Photo of a technician fitting a tyre"></div>
  <div class="shot overlay" style="left:445px;top:2495px;width:310px;height:210px;border:3px solid #1d3f70" role="img" aria-label="Photo of a wheel being serviced, shown with a hover overlay"><span class="mini"></span><span class="mini"></span></div>
  <div class="shot" style="left:775px;top:2495px;width:310px;height:210px;background:linear-gradient(135deg,#1d1f22,#6d7278 60%,#2a2c30)" role="img" aria-label="Photo of a stack of alloy wheels"></div>
  <div class="shot" style="left:115px;top:2725px;width:310px;height:270px;background:linear-gradient(135deg,#5b6168,#2b2e33)" role="img" aria-label="Photo of a mechanic working at a tyre changer"></div>
  <div class="shot" style="left:445px;top:2725px;width:310px;height:270px;background:linear-gradient(135deg,#7a4a3c,#3a3e44 55%,#c4472e)" role="img" aria-label="Photo of wheels on a workshop balancing machine"></div>
  <div class="shot" style="left:775px;top:2725px;width:310px;height:270px;background:linear-gradient(135deg,#3a3f35,#8aa53c 50%,#2b2e2a)" role="img" aria-label="Photo of a worker in a safety vest mounting a wheel"></div>
  <div class="btn btn-blue" style="left:462px;top:3025px;width:126px;height:42px">View More</div>
  <div class="btn btn-dark" style="left:608px;top:3025px;width:126px;height:42px">Get Started</div>
</section>

<section>
  <div class="abs contact"></div>
  <h2 class="abs heading section-title" style="top:3215px;font-size:46px">Get In Touch <span class="accent">With Us</span></h2>
  <p class="abs lead" style="top:3315px;font-size:13.5px">Lorem ipsum dolor sit amet, consectetur adipiscing elit, sed do eiusmod tempor incididunt ut labore et dolore magna aliqua. Quis ipsum suspendisse ultrices gravida. Risus commodo viverra maecenas accumsan lacus vel facili.</p>

  <div class="abs info" style="left:130px;top:3440px">
    <div class="icon-circle"><svg width="16" height="16" viewBox="0 0 24 24"><path fill="#fff" d="M12 2a7 7 0 0 0-7 7c0 5 7 13 7 13s7-8 7-13a7 7 0 0 0-7-7zm0 9.5A2.5 2.5 0 1 1 12 6.5a2.5 2.5 0 0 1 0 5z"/></svg></div>
    <div><h4>Location</h4><p>Dale Morrow<br>42 Orchard Lane Fairview Pa 10101</p></div>
  </div>
  <div class="abs info" style="left:130px;top:3545px">
    <div class="icon-circle"><svg width="16" height="16" viewBox="0 0 24 24"><path fill="#fff" d="M6.6 10.8a15 15 0 0 0 6.6 6.6l2.2-2.2c.3-.3.7-.4 1-.2 1.1.4 2.3.6 3.6.6.6 0 1 .4 1 1V20c0 .6-.4 1-1 1A17 17 0 0 1 3 4c0-.6.4-1 1-1h3.5c.6 0 1 .4 1 1 0 1.3.2 2.5.6 3.6.1.3 0 .7-.2 1z"/></svg></div>
    <div><h4>Contact Number</h4><p>555-214-0388</p></div>
  </div>
  <div class="abs info" style="left:130px;top:3635px">
    <div class="icon-circle"><svg width="16" height="16" viewBox="0 0 24 24"><path fill="#fff" d="M3 5h18v14H3zm2 2v.5l7 4.5 7-4.5V7z"/></svg></div>
    <div><h4>Email Address</h4><p>dale@rimcraftworks.com</p></div>
  </div>
  <div class="abs" style="left:135px;top:3745px;display:flex;gap:14px">
    <span class="social" role="img" aria-label="Social profile link"></span>
    <span class="social" role="img" aria-label="Social profile link"></span>
    <span class="social" role="img" aria-label="Social profile link"></span>
  </div>

  <div class="field" style="left:515px;top:3440px;width:265px;height:48px">First Name</div>
  <div class="field" style="left:805px;top:3440px;width:265px;height:48px">Last Name</div>
  <div class="field" style="left:515px;top:3508px;width:265px;height:48px">Email Address</div>
  <div class="field" style="left:805px;top:3508px;width:265px;height:48px">Contact Number</div>
  <div class="field" style="left:515px;top:3576px;width:555px;height:145px">Your Message Goes Here…</div>
  <div class="btn btn-blue" style="left:930px;top:3745px;width:130px;height:40px">Submit Here</div>
</section>

<footer>
  <div class="abs footer"></div>
  <div class="abs brand" style="left:0;top:3965px;width:1200px;justify-content:center;color:var(--white);font-size:34px"><span>RIMCRAFT WORKS</span><span class="brand-dot"></span></div>
  <div class="abs" style="left:150px;top:4075px;width:900px;height:1px;background:#3a3b3f"></div>
  <div class="abs foot-row" style="top:4100px;font-size:13.5px">
    <span>&#9679; 42 Orchard Lane Fairview Pa 10101</span><span>|</span><span>&#9679; 555-214-0388</span><span>|</span><span>&#9679; dale@rimcraftworks.com</span>
  </div>
  <div class="abs foot-row" style="top:4160px;gap:70px"><span>Home</span><span>Services</span><span>Gallery</span><span>Clients</span><span>Contact</span></div>
  <div class="abs" style="left:0;top:4210px;width:1200px;display:flex;justify-content:center;gap:10px">
    <span class="foot-social" role="img" aria-label="Social profile link"></span>
    <span class="foot-social" role="img" aria-label="Social profile link"></span>
    <span class="foot-social" role="img" aria-label="Social profile link"></span>
  </div>
  <p class="abs" style="left:0;top:4258px;width:1200px;text-align:center;font-size:12px;color:#c9ccd2">&copy; Copyright 2023 | All Rights Reserved</p>
</footer>

</body>
</html>
```